Create website for home automation - Control your lighting, fans, blinds etc remotely by smartphone

Plan for SHOPIFY Website - Our Clever Dwelling
Company name: Our Clever Dwelling
Company Slogan: Calm Evenings Come Naturally
Clean, Modern, Easy to Navigate, easy to maintain - not a lot of coding. We need flash technology but displaying simply what we do.
What we provide:
We will be offering wireless switch which can be added to iOS/Android App via WiFi, allowing users to remotely turn on/off connected lights, fans, security cameras, appliances, irrigation, humidifier separately from anywhere at any time.
Control your home away from home. No more wandering of your mind on those lights or appliances which you might have left switched on. No need to drive back home to check and switch them off. Save that energy, money and time just with a click of your phone no matter how far you are from home.
Replace your home electrical switches with smart switches. They retrofit existing electrical switches and allow you to make the transformation as needed.
Easy to use and intuitive app allows you to control your lights and devices just at a click. Set any kind of ambiance suiting your occasion.
Set scenes in smartphone app to group and operate your devices just at a button click. Same device can be included in more than one scene.
Collections and Products
Light Switches
Wall Plugs
Fan Switch
Pendants etc special lighting types.
Light Dimmers
Blind Controllers
Home Page:
Home page needs to telling customers what we do and how we do it in a few words to grab people.
Phone
Email
Support – Download instructions per product
Client login
Wholesale login
Promotional video to be on home screen - this is a short 1.5 - 2 min illustration introduction video to who we are and what we do - this is yet to be created)
Social media link - Facebook
Pages:
FAQ
About Us
Support/Shipping/Returns policy
Support/Installation
Blog posts
Product pages:
Description
Price
Space for where a video will be featured - how each product works/installation.
Reviews
Our competition:
http://www.brivo.com.au
https://lumigardenhub.com.au/2018/04/05/best-smart-light-switches-and-plugs/
https://www.tavelinq.com

```html
<!DOCTYPE html>
<html lang="en">
<head>
<meta charset="utf-8">
<title>Products – Our Clever Dwelling</title>
<link href="https://fonts.googleapis.com/css2?family=Outfit:wght@400;500&family=Open+Sans:wght@400&display=swap" rel="stylesheet">
<style>
  :root {
    --ink: #1c1c1c;
    --muted: #444;
    --brand: #1b4f9c;
    --band: #1a5fb4;
    --footer-bg: #0e0e0e;
    --footer-text: #e8e8e8;
    --rule: #bcbcbc;
  }
  * { box-sizing: border-box; margin: 0; padding: 0; }
  html, body { width: 1012px; height: 1200px; overflow: hidden; background: #fff; }
  body { font-family: "Open Sans", sans-serif; color: var(--ink); position: relative; }

  .site-header { height: 127px; border-bottom: 1px solid var(--rule); display: flex; align-items: center; padding: 0 70px; }
  .brand { display: flex; flex-direction: column; align-items: flex-start; width: 200px; }
  .brand-mark { width: 34px; height: 34px; border-radius: 50%; background: var(--brand); margin: 0 0 6px 50px; }
  .brand-name { font-family: "Outfit", sans-serif; font-weight: 500; font-size: 14px; color: var(--brand); letter-spacing: .3px; }
  .brand-tagline { font-family: "Outfit", sans-serif; font-weight: 500; font-size: 7px; color: var(--brand); letter-spacing: .8px; margin-left: 8px; }

  .main-nav { display: flex; gap: 26px; margin-left: 52px; font-family: "Outfit", sans-serif; font-size: 17px; }
  .main-nav a { color: var(--ink); text-decoration: none; }
  .main-nav a.active { color: var(--brand); }
  .header-tools { display: flex; gap: 18px; margin-left: 30px; align-items: center; }
  .cart { position: relative; }
  .cart-badge { position: absolute; top: -6px; left: 6px; width: 10px; height: 10px; border-radius: 50%; background: var(--brand); color: #fff; font-size: 7px; text-align: center; line-height: 10px; }

  .page-title { font-family: "Outfit", sans-serif; font-weight: 400; font-size: 40px; text-align: center; margin-top: 62px; }

  .product-grid { display: grid; grid-template-columns: 245px 245px 245px; column-gap: 50px; row-gap: 40px; margin: 34px 0 0 84px; width: 850px; }
  .product-grid .product-card:nth-child(3n+2) { margin-left: -2px; }
  .product-grid .product-card:nth-child(3n) { margin-left: 4px; }
  .product-image { height: 180px; box-shadow: 0 0 10px rgba(0,0,0,.08); border: 2px solid #fafafa; }
  .product-name { font-family: "Outfit", sans-serif; font-weight: 400; font-size: 20px; line-height: 24px; margin: 14px 0 6px -2px; }
  .product-desc { font-size: 14px; color: var(--muted); margin-left: -2px; }

  .img-lights { background: linear-gradient(160deg, #e8d48a 0%, #6b5a44 40%, #2a2622 75%, #c9a86a 100%); }
  .img-plugs { background: linear-gradient(90deg, #9aa0a6 0%, #c3c6ca 45%, #2d2d2f 70%, #b5b0aa 100%); }
  .img-fan { background: linear-gradient(120deg, #4a4a4c 0%, #8d8f92 50%, #d3d3d3 100%); }
  .img-phone { background: linear-gradient(100deg, #4a3c32 0%, #d8cfc4 45%, #c9a58b 75%, #8a8a8a 100%); }
  .img-dimmer { background: radial-gradient(ellipse at 50% 60%, #ffcc55 0%, #e57a12 45%, #9a3606 100%); }
  .img-blinds { background: linear-gradient(140deg, #8fa3a6 0%, #4ea65b 40%, #1f6fb5 65%, #d9c3b2 100%); }

  .footer-band { position: absolute; top: 910px; left: 0; width: 1012px; height: 8px; background: var(--band); }
  .site-footer { position: absolute; top: 918px; left: 0; width: 1012px; height: 282px; background: var(--footer-bg); color: var(--footer-text); }
  .footer-col { position: absolute; top: 57px; }
  .footer-col h3 { font-weight: 400; font-size: 14px; margin-bottom: 18px; }
  .footer-col ul { list-style: none; font-size: 12px; }
  .footer-col li { margin-bottom: 5px; }
  .footer-col li::before { content: "» "; }
  .col-info { left: 78px; }
  .col-links { left: 302px; top: 59px; }
  .col-contact { left: 474px; }
  .col-contact p { font-size: 12px; line-height: 19px; margin: 0 0 5px 3px; }
  .col-follow { left: 780px; top: 54px; }
  .social { display: flex; gap: 12px; margin: 28px 0 0 0; }
  .social span { width: 21px; height: 21px; border-radius: 4px; background: #fff; display: block; }
  .footer-rule { position: absolute; top: 218px; left: 72px; width: 864px; border-top: 1px solid #2a2a2a; }
  .copyright { position: absolute; top: 238px; left: 0; width: 1012px; text-align: center; font-size: 13px; }
</style>
</head>
<body>
  <header class="site-header">
    <div class="brand">
      <span class="brand-mark"></span>
      <span class="brand-name">OUR CLEVER DWELLING</span>
      <span class="brand-tagline">Calm Evenings Come Naturally</span>
    </div>
    <nav class="main-nav">
      <a href="#">Home</a><a href="#">About Us</a><a href="#" class="active">Products</a><a href="#">Support</a><a href="#">Blog</a><a href="#">FAQ</a><a href="#">Contact</a>
    </nav>
    <div class="header-tools">
      <svg width="16" height="16" viewBox="0 0 16 16" aria-label="Search"><circle cx="6.5" cy="6.5" r="4.8" fill="none" stroke="#111" stroke-width="2.4"/><line x1="10" y1="10" x2="14.5" y2="14.5" stroke="#111" stroke-width="2.8" stroke-linecap="round"/></svg>
      <span class="cart">
        <span class="cart-badge">1</span>
        <svg width="18" height="15" viewBox="0 0 18 15" aria-label="Cart"><path d="M1 5h16l-2 9H3z" fill="#111"/><path d="M5 5l3-4M13 5l-3-4" stroke="#111" stroke-width="1.6"/><path d="M6 7v5M9 7v5M12 7v5" stroke="#fff" stroke-width="1.2"/></svg>
      </span>
      <svg width="17" height="17" viewBox="0 0 17 17" aria-label="Account" style="margin-left:14px"><circle cx="8.5" cy="5" r="4" fill="#111"/><path d="M1 17c0-5 3-7.5 7.5-7.5S16 12 16 17z" fill="#111"/></svg>
    </div>
  </header>

  <h1 class="page-title">Products</h1>

  <main class="product-grid">
    <article class="product-card">
      <div class="product-image img-lights" role="img" aria-label="Modern living room lit by a ring pendant light"></div>
      <h2 class="product-name">Light Switches</h2>
      <p class="product-desc">Neque porro quisquam est dolorem</p>
    </article>
    <article class="product-card">
      <div class="product-image img-plugs" role="img" aria-label="Smart wall panel mounted beside a doorway"></div>
      <h2 class="product-name">Wall Plugs</h2>
      <p class="product-desc">Neque porro quisquam est dolorem</p>
    </article>
    <article class="product-card">
      <div class="product-image img-fan" role="img" aria-label="Hand holding a remote in front of a standing fan"></div>
      <h2 class="product-name">Fan Switch</h2>
      <p class="product-desc">Neque porro quisquam est dolorem</p>
    </article>
    <article class="product-card">
      <div class="product-image img-phone" role="img" aria-label="Hands using a home control app on a smartphone in a living room"></div>
      <h2 class="product-name">Pendants etc special lighting types.</h2>
      <p class="product-desc">Neque porro quisquam est dolorem</p>
    </article>
    <article class="product-card">
      <div class="product-image img-dimmer" role="img" aria-label="Warm glowing bulb under a lamp shade"></div>
      <h2 class="product-name">Light Dimmers</h2>
      <p class="product-desc">Neque porro quisquam est dolorem</p>
    </article>
    <article class="product-card">
      <div class="product-image img-blinds" role="img" aria-label="Smartphone showing home control icons held in hands"></div>
      <h2 class="product-name">Blind Controllers</h2>
      <p class="product-desc">Neque porro quisquam est dolorem</p>
    </article>
  </main>

  <div class="footer-band"></div>
  <footer class="site-footer">
    <div class="footer-col col-info">
      <h3>INFORMATION</h3>
      <ul><li>Privacy Policy</li><li>Your Account</li><li>Advanced Search</li><li>Contact Us</li></ul>
    </div>
    <div class="footer-col col-links">
      <h3>LINKS</h3>
      <ul><li>Home</li><li>About us</li><li>Products</li><li>Shop</li></ul>
    </div>
    <div class="footer-col col-contact">
      <h3>CONTACT US</h3>
      <p>Address : 42-48 Marlow - Kessing Road,<br>Kessing, Canada</p>
      <p>Phone :&nbsp; (03) 9416 2275,&nbsp; (04) 3278 0519</p>
      <p>Email : sales@cleverdwelling.com.au</p>
    </div>
    <div class="footer-col col-follow">
      <h3>FOLLOW US OUT THERE</h3>
      <div class="social"><span></span><span></span><span></span><span></span></div>
    </div>
    <div class="footer-rule"></div>
    <p class="copyright">Copyright © 2018. All Rights Reserved</p>
  </footer>
</body>
</html>
```